Los Brava Dip – CPG Website with WordPress - Store Locator: WP Maps plugin

Larkfield Food Company is a startup consumer packaged goods (CPG) brand launching its flagship product line — Los Brava Dip. We’re seeking a talented web designer to create a bold, professional, mobile-optimized website using WordPress with a WP Maps store locator to help customers find local retailers.

Our goal is to build a strong online presence that supports both retail growth and direct-to-consumer sales.

See Los Brava _Website_Design_Brief word document.

The website URL is https://losbravadip.example/

Target Market(s)

Consumers of gourmet salsa

Industry/Entity Type

Consumer Packaged Goods - Salsa manufacturer.

Coding

Coded - Design and coding required

Number of Pages Required

5+ page

Requirements
Must have
• The design of the Los Brava Dip website shall emulate the clean, polished aesthetic of Fennigo.example.

```html
<!DOCTYPE html>
<html lang="en">
<head>
<meta charset="utf-8">
<title>Reviews – Los Brava Dip</title>
<link href="https://fonts.googleapis.com/css2?family=Roboto+Condensed:wght@700&family=Outfit:wght@400;500;600&display=swap" rel="stylesheet">
<style>
:root{
  --red:#c8161d;
  --bar:#9b0000;
  --track:#f3f3f3;
  --ink:#231f20;
  --gold:#eaa52c;
  --card-dark:#231807;
  --star:#f5a623;
  --border:#b9b9b9;
}
*{box-sizing:border-box;margin:0;padding:0}
html,body{width:1200px;height:2818px;overflow:hidden;background:#fff}
body{font-family:"Outfit",sans-serif;color:var(--ink);position:relative}
.heading{font-family:"Roboto Condensed",sans-serif;font-weight:700;text-transform:uppercase}

/* header */
.site-header{position:absolute;top:0;left:0;width:1200px;height:79px;background:#fff;z-index:3}
.brand{position:absolute;left:100px;top:-60px;width:164px;height:164px;border-radius:50%;background:#fff;display:flex;align-items:flex-end;justify-content:center;padding-bottom:52px}
.brand span{font-family:"Roboto Condensed",sans-serif;font-weight:700;font-size:36px;color:var(--red)}
.main-nav{position:absolute;left:326px;top:34px;display:flex;gap:0}
.main-nav a{font-size:13.5px;font-weight:500;letter-spacing:1.3px;color:var(--ink);text-decoration:none;margin-right:54px;position:relative}
.main-nav a.current::after{content:"";position:absolute;left:0;right:0;bottom:-10px;height:2px;background:var(--red)}

/* hero */
.hero{position:absolute;top:79px;left:0;width:1200px;height:324px;background:linear-gradient(110deg,#f2a31c 0%,#ec8a12 30%,#e2530c 50%,#a42412 68%,#5c1409 85%,#3a1508 100%)}
.hero h1{position:absolute;top:118px;width:100%;text-align:center;color:#fff;font-size:62px;letter-spacing:1px}
.hero .swash{position:absolute;left:498px;top:185px}

/* intro */
.eyebrow{font-size:14.5px;font-weight:600;letter-spacing:2.4px;color:var(--red);text-transform:uppercase;text-align:center}
.eyebrow span{border-top:1px solid var(--red);border-bottom:1px solid var(--red);padding:3px 3px 2px}
.intro .eyebrow{position:absolute;top:465px;width:100%;left:-16px}
.intro h2{position:absolute;top:490px;width:100%;text-align:center;font-size:43px;letter-spacing:1px;left:-10px}
.intro .swash{position:absolute;left:470px;top:538px}
.intro-copy{position:absolute;top:580px;left:120px;width:940px;text-align:center;font-size:19.5px;line-height:27.5px}
.intro-copy p{margin-bottom:29px}

/* rating cards */
.rating-card{position:absolute;width:463px;height:270px;border:2px solid var(--border);background:#fff}
.rating-card h3{position:absolute;left:42px;top:28px;font-size:27px;color:var(--red);letter-spacing:.5px}
.rating-rows{position:absolute;left:40px;top:78px}
.rating-row{display:flex;align-items:center;height:32px}
.rating-row .stars{color:var(--bar);font-size:19px;width:106px;letter-spacing:-1px}
.rating-row .count{font-size:15px;width:38px}
.rating-row .track{width:178px;height:16px;background:var(--track);position:relative}
.rating-row .fill{position:absolute;left:0;top:0;height:16px;background:var(--bar)}

/* customer reviews */
.customer-reviews{position:absolute;top:1821px;left:0;width:1200px;height:520px;background:linear-gradient(135deg,#f0b234 0%,#e9a428 60%,#e39a22 100%)}
.customer-reviews .eyebrow{position:absolute;top:72px;width:100%;left:-34px;color:#fff}
.customer-reviews .eyebrow span{border-color:#fff}
.customer-reviews h2{position:absolute;top:94px;width:100%;left:-40px;text-align:center;color:#fff;font-size:37px;letter-spacing:1px}
.customer-reviews .swash{position:absolute;left:478px;top:134px}
.summary{position:absolute;top:170px;left:460px;display:flex;align-items:center;gap:8px;color:#fff;font-size:12.5px;font-weight:600}
.summary .stars{font-size:18px;letter-spacing:3px}
.review-card{position:absolute;top:230px;width:315px;height:175px;background:var(--card-dark);color:#fff;padding:30px 32px;font-size:16.5px;line-height:27px;font-weight:500}
.review-card .stars{color:var(--star);font-size:18px;letter-spacing:4px;display:block;line-height:18px;margin-bottom:10px}
.slider-arrows{position:absolute;top:436px;left:534px;display:flex;gap:20px}

/* follow */
.follow{position:absolute;top:2341px;left:0;width:1200px;height:278px;background:linear-gradient(100deg,#d9461e 0%,#d93a1c 40%,#b71e1e 65%,#9b1618 100%)}
.follow h2{position:absolute;left:375px;top:54px;width:406px;border-top:1px solid #fff;border-bottom:1px solid #fff;padding:8px 0 9px;text-align:center;color:#fff;font-family:"Outfit",sans-serif;font-weight:600;font-size:30px;letter-spacing:.5px}
.social{position:absolute;top:138px;width:80px;height:80px;border:2px solid #fff;border-radius:50%;display:flex;align-items:center;justify-content:center;color:#fff;font-size:13px;font-weight:600;text-decoration:none}

/* footer */
.site-footer{position:absolute;top:2619px;left:0;width:1200px;height:199px;background:#fff}
.footer-brand{position:absolute;left:0;top:0;width:299px;height:199px;border-right:1px solid #ddd;display:flex;align-items:center;justify-content:center}
.footer-brand span{font-family:"Roboto Condensed",sans-serif;font-weight:700;font-size:46px;color:var(--red)}
.footer-nav{position:absolute;left:353px;top:64px;display:flex;align-items:center}
.footer-nav a{font-size:13.5px;font-weight:500;letter-spacing:1.3px;color:var(--ink);text-decoration:none}
.footer-nav i{display:inline-block;width:5px;height:5px;background:var(--red);margin:0 24px}
.footer-bottom{position:absolute;left:300px;top:116px;width:888px;border-top:1px solid #ddd}
.copyright{position:absolute;left:48px;top:28px;font-size:13px}
.footer-social{position:absolute;left:494px;top:20px;display:flex;gap:6px}
.footer-social span{width:26px;height:26px;border-radius:50%;background:var(--ink)}
.legal{position:absolute;left:582px;top:28px;font-size:13px;display:flex;gap:16px}
.legal a{color:var(--ink);text-decoration:none}
</style>
</head>
<body>

<header class="site-header">
  <div class="brand"><span>Los Brava</span></div>
  <nav class="main-nav">
    <a href="#">ABOUT</a><a href="#">PRODUCTS</a><a href="#">WHERE TO BUY</a><a href="#">RECIPES</a><a href="#" class="current">REVIEWS</a>
  </nav>
</header>

<section class="hero" role="img" aria-label="Abstract flame illustration in orange, red and deep green">
  <h1 class="heading">Reviews</h1>
  <svg class="swash" width="264" height="16" viewBox="0 0 264 16"><path d="M4 13 Q120 2 260 8" stroke="#fff" stroke-width="5" fill="none" stroke-linecap="round"/></svg>
</section>

<section class="intro">
  <p class="eyebrow"><span>Our Reviews</span></p>
  <h2 class="heading">Blind Taste Test Results – June 2025</h2>
  <svg class="swash" width="240" height="14" viewBox="0 0 240 14"><path d="M4 10 Q110 2 236 8" stroke="#c8161d" stroke-width="4" fill="none" stroke-linecap="round"/></svg>
  <div class="intro-copy">
    <p>In June 2025, Los Brava Dip was put to the test in a blind taste challenge conducted by a third party with 38 participants. Without knowing the brand, tasters judged flavor, heat level balance, aroma, appearance, and overall satisfaction.</p>
    <p>The result?</p>
    <p>An impressive 4.2 out of 5 stars, with 79% of participants rating it 5 stars.<br>These reviews reflect the authentic flavor and bold character that make Los Brava stand out in a crowded salsa market. Taste-tested, crowd-approved.</p>
  </div>
</section>

<article class="rating-card" style="left:124px;top:895px">
  <h3 class="heading">Flavor</h3>
  <div class="rating-rows">
    <div class="rating-row"><span class="stars">★★★★★</span><span class="count">17</span><span class="track"><span class="fill" style="width:147px"></span></span></div>
    <div class="rating-row"><span class="stars">★★★★☆</span><span class="count">12</span><span class="track"><span class="fill" style="width:122px"></span></span></div>
    <div class="rating-row"><span class="stars">★★★☆☆</span><span class="count">4</span><span class="track"><span class="fill" style="width:40px"></span></span></div>
    <div class="rating-row"><span class="stars">★★☆☆☆</span><span class="count">1</span><span class="track"><span class="fill" style="width:8px"></span></span></div>
    <div class="rating-row"><span class="stars">★☆☆☆☆</span><span class="count">0</span><span class="track"></span></div>
  </div>
</article>

<article class="rating-card" style="left:603px;top:895px">
  <h3 class="heading">Heat Level Balance</h3>
  <div class="rating-rows">
    <div class="rating-row"><span class="stars">★★★★★</span><span class="count">13</span><span class="track"><span class="fill" style="width:147px"></span></span></div>
    <div class="rating-row"><span class="stars">★★★★☆</span><span class="count">21</span><span class="track"><span class="fill" style="width:154px"></span></span></div>
    <div class="rating-row"><span class="stars">★★★☆☆</span><span class="count">4</span><span class="track"><span class="fill" style="width:46px"></span></span></div>
    <div class="rating-row"><span class="stars">★★☆☆☆</span><span class="count">0</span><span class="track"></span></div>
    <div class="rating-row"><span class="stars">★☆☆☆☆</span><span class="count">0</span><span class="track"></span></div>
  </div>
</article>

<article class="rating-card" style="left:122px;top:1181px">
  <h3 class="heading">Aroma</h3>
  <div class="rating-rows">
    <div class="rating-row"><span class="stars">★★★★★</span><span class="count">20</span><span class="track"><span class="fill" style="width:147px"></span></span></div>
    <div class="rating-row"><span class="stars">★★★★☆</span><span class="count">13</span><span class="track"><span class="fill" style="width:90px"></span></span></div>
    <div class="rating-row"><span class="stars">★★★☆☆</span><span class="count">5</span><span class="track"><span class="fill" style="width:28px"></span></span></div>
    <div class="rating-row"><span class="stars">★★☆☆☆</span><span class="count">0</span><span class="track"></span></div>
    <div class="rating-row"><span class="stars">★☆☆☆☆</span><span class="count">0</span><span class="track"></span></div>
  </div>
</article>

<article class="rating-card" style="left:601px;top:1181px">
  <h3 class="heading">Appearance</h3>
  <div class="rating-rows">
    <div class="rating-row"><span class="stars">★★★★★</span><span class="count">20</span><span class="track"><span class="fill" style="width:147px"></span></span></div>
    <div class="rating-row"><span class="stars">★★★★☆</span><span class="count">0</span><span class="track"></span></div>
    <div class="rating-row"><span class="stars">★★★☆☆</span><span class="count">0</span><span class="track"></span></div>
    <div class="rating-row"><span class="stars">★★☆☆☆</span><span class="count">0</span><span class="track"></span></div>
    <div class="rating-row"><span class="stars">★☆☆☆☆</span><span class="count">0</span><span class="track"></span></div>
  </div>
</article>

<article class="rating-card" style="left:124px;top:1471px;height:280px">
  <h3 class="heading">Overall Satisfaction</h3>
  <div class="rating-rows" style="left:44px">
    <div class="rating-row"><span class="stars">★★★★★</span><span class="count">11</span><span class="track"><span class="fill" style="width:82px"></span></span></div>
    <div class="rating-row"><span class="stars">★★★★☆</span><span class="count">24</span><span class="track"><span class="fill" style="width:122px"></span></span></div>
    <div class="rating-row"><span class="stars">★★★☆☆</span><span class="count">3</span><span class="track"><span class="fill" style="width:25px"></span></span></div>
    <div class="rating-row"><span class="stars">★★☆☆☆</span><span class="count">1</span><span class="track"><span class="fill" style="width:5px"></span></span></div>
    <div class="rating-row"><span class="stars">★☆☆☆☆</span><span class="count">0</span><span class="track"></span></div>
  </div>
</article>

<section class="customer-reviews">
  <p class="eyebrow"><span>What People Say</span></p>
  <h2 class="heading">Customer Reviews</h2>
  <svg class="swash" width="150" height="10" viewBox="0 0 150 10"><path d="M3 7 Q75 2 147 5" stroke="#c8161d" stroke-width="3" fill="none" stroke-linecap="round"/></svg>
  <div class="summary"><span class="stars">★★★★★</span><span>4.2 from 38 Reviews</span></div>
  <div class="review-card" style="left:108px"><span class="stars">★★★★★</span>Very good, and I'm a salsa snob!"</div>
  <div class="review-card" style="left:443px;padding-top:30px"><span class="stars" style="margin-bottom:14px">★★★★★</span>“Very nice overall. I cook a lot so I often make my own, but this is great!"</div>
  <div class="review-card" style="left:774px;top:228px"><span class="stars">★★★★★</span>“Really good flavor."</div>
  <div class="slider-arrows">
    <svg width="30" height="38" viewBox="0 0 30 38" aria-label="Previous"><path d="M22 3 L8 19 L22 35" stroke="#fff" stroke-width="2.5" fill="none"/></svg>
    <svg width="30" height="38" viewBox="0 0 30 38" aria-label="Next"><path d="M8 3 L22 19 L8 35" stroke="#fff" stroke-width="2.5" fill="none"/></svg>
  </div>
</section>

<section class="follow">
  <h2>FOLLOW US ON</h2>
  <a class="social" href="#" style="left:484px">Friendly</a>
  <a class="social" href="#" style="left:588px">Picturo</a>
</section>

<footer class="site-footer">
  <div class="footer-brand"><span>Los Brava</span></div>
  <nav class="footer-nav">
    <a href="#">ABOUT</a><i></i><a href="#">PRODUCTS</a><i></i><a href="#">WHERE TO BUY</a><i></i><a href="#">RECIPES</a><i></i><a href="#">REVIEWS</a><i></i><a href="#">CONTACT</a>
  </nav>
  <div class="footer-bottom">
    <p class="copyright">© 2025 Larkfield Food Company. All rights reserved.</p>
    <div class="footer-social"><span aria-label="Friendly"></span><span aria-label="Picturo"></span></div>
    <div class="legal"><a href="#">Privacy Policy</a><a href="#">Terms of Use</a></div>
  </div>
</footer>

</body>
</html>
```